Business card for law firm

Need business card for new law firm. Think confident, authoritative, conservative, but not stuffy or old-fashioned.

Contact Information for Business Card

Content for card - logo (uploaded), plus the following:

Paul Whitcombe (larger font)
Managing Partner (larger font, but not as large as name)
Level 9, 7 Ferris Lane
Sydney NSW 2000
Main Tel 02 9364 2710
Direct Tel 02 8472 3159
Email paul@qvlegal.com.au
www.qvlegal.com.au

Letterhead design should include logo plus:
Level 9, 7 Ferris Lane
Sydney NSW 2000
Tel 02 8472 3159
www.qvlegal.com.au

```html
<!DOCTYPE html>
<html lang="en">
<head>
<meta charset="utf-8">
<title>Quayvale Lawyers – Letterhead</title>
<link href="https://fonts.googleapis.com/css2?family=Open+Sans:wght@400;600&family=Lato:wght@400&display=swap" rel="stylesheet">
<style>
  :root {
    --navy: #0d1f5c;
    --ink: #4a4a4a;
    --ink-dark: #333333;
    --paper: #ffffff;
    --black: #111111;
  }
  html, body {
    margin: 0;
    padding: 0;
    width: 1040px;
    height: 1200px;
    overflow: hidden;
    background: var(--paper);
  }
  .letterhead {
    position: relative;
    width: 1040px;
    height: 1200px;
    background: var(--paper);
    font-family: "Open Sans", Arial, sans-serif;
    color: var(--ink);
  }
  .side-band {
    position: absolute;
    left: 0; top: 0;
    width: 17px; height: 100%;
    background: var(--navy);
  }
  .brand {
    position: absolute;
    top: 52px;
    right: 100px;
    width: 300px;
    display: flex;
    flex-direction: column;
    align-items: center;
    gap: 34px;
  }
  .brand-square {
    width: 68px; height: 68px;
    background: var(--navy);
  }
  .brand-name {
    font-family: "Open Sans", Arial, sans-serif;
    font-weight: 600;
    font-size: 30px;
    letter-spacing: 1px;
    color: var(--black);
    white-space: nowrap;
  }
  .letter {
    position: absolute;
    left: 99px;
    top: 214px;
    width: 839px;
    font-size: 16px;
    line-height: 27px;
  }
  .letter p { margin: 0; }
  .issue-date { margin-bottom: 10px !important; }
  .recipient { line-height: 19px; margin-bottom: 48px !important; }
  .salutation { margin-bottom: 27px !important; }
  .body-copy { text-align: justify; hyphens: auto; -webkit-hyphens: auto; margin-bottom: 27px !important; }
  .closing { margin-top: 53px !important; margin-bottom: 52px !important; }
  .signatory-name { font-size: 19px; color: var(--ink-dark); line-height: 28px; }
  .signatory-role { font-size: 15px; line-height: 22px; }
  .corner-block {
    position: absolute;
    left: 0; bottom: 0;
    width: 92px; height: 104px;
    background: var(--navy);
  }
  .contact-bar {
    position: absolute;
    top: 1150px;
    left: 118px;
    right: 100px;
    display: flex;
    align-items: center;
    gap: 30px;
    font-family: "Lato", Arial, sans-serif;
    font-size: 18px;
    color: var(--black);
  }
  .contact-item { display: flex; align-items: center; gap: 8px; white-space: nowrap; }
  .contact-item.address { margin-left: 14px; }
  .contact-icon { width: 20px; height: 20px; flex: none; }
</style>
</head>
<body>
<main class="letterhead">
  <div class="side-band"></div>

  <header class="brand">
    <div class="brand-square"></div>
    <div class="brand-name">QUAYVALE LAWYERS</div>
  </header>

  <section class="letter">
    <p class="issue-date">Issuing Date: May 5, 2018</p>
    <p class="recipient">Name Of Employee Mr. XYZABC<br>Address of Employee<br>Address Line 2 etc..</p>
    <p class="salutation">Dear Mr.XYZABC</p>
    <p class="body-copy">Lorem Ipsum has been the industry's standard dummy text ever since the 1500s, when an unknown printer took a galley of type and scrambled it to make a type specimen book. It has survived not only five centuries, but also the leap into electronic typesetting, remaining essentially unchanged. It was popularised in the 1960s with the release of Typeline sheets containing Lorem Ipsum passages, and more recently with desktop publishing software like Folio PageMaster including versions of Lorem Ipsum.</p>
    <p class="body-copy">Lorem Ipsum is simply dummy text of the printing and typesetting industry. Lorem Ipsum has been the industry's standard dummy text ever since the 1500s, when an unknown printer took a galley of type and scrambled it to make a type specimen book.</p>
    <p class="body-copy">It has survived not only five centuries, but also the leap into electronic typesetting, remaining essentially unchanged. It was popularised in the 1960s with the release of Typeline sheets containing Lorem IpsumIpsum passages.</p>
    <p class="closing">Yours Sincerely</p>
    <p class="signatory-name">Daniel Ashford</p>
    <p class="signatory-role">Managing Director</p>
  </section>

  <div class="corner-block"></div>

  <footer class="contact-bar">
    <span class="contact-item">
      <svg class="contact-icon" viewBox="0 0 20 20" aria-hidden="true">
        <rect width="20" height="20" rx="3" fill="var(--navy)"/>
        <path d="M6.2 4.5l2 .3.8 2.6-1.3 1.1c.7 1.5 1.8 2.6 3.3 3.3l1.1-1.3 2.6.8.3 2c-.1.6-.6 1-1.2 1C8.6 14.2 5.8 11.4 5.2 5.7c0-.6.4-1.1 1-1.2z" fill="#fff"/>
      </svg>
      02 8472 3159
    </span>
    <span class="contact-item">
      <svg class="contact-icon" viewBox="0 0 20 20" aria-hidden="true">
        <rect width="20" height="20" rx="3" fill="var(--navy)"/>
        <circle cx="10" cy="10" r="5.5" fill="none" stroke="#fff" stroke-width="1.6"/>
        <path d="M4.5 10h11M10 4.5c2 2 2 9 0 11M10 4.5c-2 2-2 9 0 11" fill="none" stroke="#fff" stroke-width="1.1"/>
      </svg>
      www.qvlegal.com.au
    </span>
    <span class="contact-item address">
      <svg class="contact-icon" viewBox="0 0 20 20" aria-hidden="true">
        <rect width="20" height="20" rx="3" fill="var(--navy)"/>
        <path d="M10 3.8c-2.4 0-4.2 1.8-4.2 4.1 0 3 4.2 8.2 4.2 8.2s4.2-5.2 4.2-8.2c0-2.3-1.8-4.1-4.2-4.1z" fill="#fff"/>
        <circle cx="10" cy="8" r="1.6" fill="var(--navy)"/>
      </svg>
      Level 9, 7 Ferris Lane Sydney NSW 2000
    </span>
  </footer>
</main>
</body>
</html>
```